Southern Plantskills Academy needs a modern website that oozes professionalism

Our current website is boring and looks like everyone elses. We need a modern website that says we are the best at plant operator training. We use Brontovex and Hiraketo equipment for our training. We train all over Australia in Civil Construction, Mining and Quarrying. We want to be the "Go to" website for all plant operator training in Australia.

Industry/Entity Type

Heavy Machinery Training

Colors
0054AA
0677BA
7BADD7
CADEEF
E8F1F8
FFF300
FFF600
FEFA6F
FFFEC7
FFFEE8

```html
<!DOCTYPE html>
<html lang="en">
<head>
<meta charset="utf-8">
<title>Southern Plantskills Academy</title>
<link href="https://fonts.googleapis.com/css2?family=Poppins:wght@700;800&family=Roboto:wght@400;500;700&family=Roboto+Slab:wght@600&display=swap" rel="stylesheet">
<style>
:root{
  --navy:#0b3c66;
  --navy-deep:#0a3358;
  --yellow:#fcc80a;
  --ink:#1d1d1d;
  --grey:#6f6f6f;
  --white:#ffffff;
  --night:#0a0608;
}
*{margin:0;padding:0;box-sizing:border-box}
html,body{width:1200px;height:3026px;overflow:hidden;background:var(--white)}
body{position:relative;font-family:"Roboto",sans-serif;color:var(--ink)}
.abs{position:absolute}
.btn{position:absolute;display:flex;align-items:center;justify-content:center;border-radius:22px;font-family:"Roboto Slab",serif;font-weight:600;font-size:13px;text-transform:uppercase;color:var(--white)}
.btn-yellow{background:var(--yellow)}
.btn-navy{background:var(--navy)}

/* header */
.site-header{position:absolute;left:0;top:0;width:1200px;height:80px;background:var(--white)}
.brand{position:absolute;left:143px;top:20px;display:flex;align-items:center;gap:10px}
.brand-dot{width:34px;height:34px;border-radius:50%;background:var(--navy)}
.brand-name{font-family:"Roboto",sans-serif;font-weight:700;font-size:18px;color:var(--navy);line-height:1.1;width:190px}
.header-phone{position:absolute;left:534px;top:26px;display:flex;align-items:center;gap:8px;font-size:23px;font-weight:500;color:#3a3a3a}
.phone-badge{width:27px;height:27px;border-radius:50%;background:var(--yellow);display:flex;align-items:center;justify-content:center}
.main-nav{position:absolute;left:0;top:80px;width:1200px;height:46px;background:var(--navy)}
.main-nav ul{list-style:none;position:absolute;left:144px;top:0;display:flex;height:46px}
.main-nav li{font-size:13px;font-weight:700;color:var(--white);padding:0 16px;display:flex;align-items:center}
.main-nav li.active{background:var(--yellow)}

/* hero */
.hero{position:absolute;left:0;top:126px;width:1200px;height:496px;overflow:hidden}
.hero-photo{position:absolute;inset:0;background:linear-gradient(180deg,#7f8a93 0%,#a9b1b5 30%,#8d8a78 55%,#6f6a5c 100%)}
.hero-photo::after{content:"";position:absolute;left:520px;top:70px;width:420px;height:260px;background:radial-gradient(ellipse at center,rgba(214,178,38,.85) 0%,rgba(180,150,40,.5) 45%,rgba(0,0,0,0) 70%)}
.hero-title{position:absolute;left:144px;top:70px;font-family:"Poppins",sans-serif;font-weight:800;font-size:43px;line-height:49px;color:var(--white);text-transform:uppercase}
.hero-sub{position:absolute;left:144px;top:177px;font-size:21px;font-weight:500;line-height:31px;color:var(--white)}
.hero-dots{position:absolute;left:1137px;top:122px;display:flex;flex-direction:column;gap:11px}
.hero-dots span{width:8px;height:8px;border-radius:50%;background:var(--white)}
.hero-dots span.on{background:var(--yellow)}
.hero-curve{position:absolute;left:0;top:0}

/* services */
.section-title{font-family:"Poppins",sans-serif;font-weight:800;color:var(--navy);text-transform:uppercase}
.services-title{position:absolute;left:0;top:672px;width:1200px;text-align:center;font-size:45px}
.service{position:absolute;top:758px;width:221px}
.service-photo{width:221px;height:182px}
.service-name{margin-top:18px;text-align:center;font-size:14px;font-weight:500;line-height:19px;color:#222;text-transform:uppercase}
.carousel-arrow{position:absolute;top:828px;width:44px;height:44px;border-radius:50%;border:1.5px solid #555;background:var(--white);display:flex;align-items:center;justify-content:center}

/* promo */
.promo{position:absolute;left:0;top:1048px;width:1200px;height:533px;background:var(--navy)}
.promo-art{position:absolute;left:0;top:0}
.promo-head{position:absolute;left:143px;top:66px;font-size:26px;font-weight:500;line-height:39px;color:var(--white);text-transform:uppercase}
.promo-text{position:absolute;left:144px;top:156px;font-size:15px;line-height:22px;color:var(--white);width:440px}
.promo-prize{position:absolute;left:144px;top:218px;font-size:30px;font-weight:700;line-height:34px;color:var(--yellow);text-transform:uppercase}
.promo-small{position:absolute;left:144px;font-size:13.5px;line-height:19px;color:var(--white);width:460px}

/* trusted */
.trusted{position:absolute;left:0;top:1581px;width:1200px;height:431px}
.trusted-photo{position:absolute;left:0;top:0;width:760px;height:431px;background:linear-gradient(90deg,#5e5a4e 0%,#8a7a52 35%,#b79a5a 55%,rgba(205,205,205,.7) 82%,rgba(255,255,255,1) 100%)}
.trusted-title{position:absolute;left:622px;top:80px;font-size:45px;line-height:49px}
.trusted-text{position:absolute;left:622px;top:203px;width:440px;font-size:15.5px;line-height:26px;color:var(--grey)}

/* why */
.why{position:absolute;left:0;top:2012px;width:1200px;height:620px;background:var(--yellow)}
.why-photo{position:absolute;left:600px;top:0;width:600px;height:520px;background:linear-gradient(160deg,#6f9cc4 0%,#a9c2d6 35%,#d8aa2c 60%,#8a6f2a 100%)}
.why-title{position:absolute;left:146px;top:85px;font-size:45px}
.why-text{position:absolute;left:147px;top:150px;width:412px;font-size:15.5px;line-height:26px;color:#3e3a2a;text-align:justify}
.why-item{position:absolute;left:146px;display:flex;gap:10px}
.why-tick{width:24px;height:24px;border-radius:50%;background:var(--navy);display:flex;align-items:center;justify-content:center;margin-top:2px}
.why-item h3{font-size:19px;font-weight:500;color:var(--navy);text-transform:uppercase;line-height:24px}
.why-item p{font-size:12.5px;color:#5a5130;margin-top:6px}

/* footer */
.site-footer{position:absolute;left:0;top:2532px;width:1200px;height:494px}
.footer-curve{position:absolute;left:0;top:0}
.contact{position:absolute;top:237px;display:flex;gap:16px;color:var(--white)}
.contact-icon{width:58px;height:58px;border-radius:50%;border:2px solid var(--white);display:flex;align-items:center;justify-content:center;flex:none}
.contact-icon.filled{background:var(--yellow);border-color:var(--yellow)}
.contact h4{font-size:13px;font-weight:700;text-transform:uppercase;margin-top:8px}
.contact p{font-size:11.5px;line-height:24px;margin-top:2px}
.contact-divider{position:absolute;top:250px;width:1px;height:38px;background:#555}
.footer-nav{position:absolute;left:0;top:342px;width:1200px;display:flex;justify-content:center;gap:32px;list-style:none}
.footer-nav li{font-size:13px;font-weight:700;color:var(--white)}
.copyright{position:absolute;left:0;top:384px;width:1200px;text-align:center;font-size:13px;color:var(--white)}
.socials{position:absolute;left:556px;top:432px;display:flex;gap:8px}
.socials span{width:24px;height:24px}
</style>
</head>
<body>

<header class="site-header">
  <div class="brand"><span class="brand-dot"></span><span class="brand-name">Southern Plantskills Academy</span></div>
  <div class="header-phone">
    <span class="phone-badge"><svg width="14" height="14" viewBox="0 0 24 24"><path d="M6.6 10.8a15 15 0 0 0 6.6 6.6l2.2-2.2c.3-.3.7-.4 1-.2 1.1.4 2.3.6 3.6.6.6 0 1 .4 1 1V20c0 .6-.4 1-1 1A17 17 0 0 1 3 4c0-.6.4-1 1-1h3.5c.6 0 1 .4 1 1 0 1.3.2 2.5.6 3.6.1.3 0 .7-.2 1z" fill="#fff"/></svg></span>
    1300 555 018
  </div>
  <span class="btn btn-yellow" style="left:724px;top:19px;width:164px;height:37px">Course Calendar</span>
  <span class="btn btn-navy" style="left:892px;top:19px;width:165px;height:37px">Student Handbook</span>
</header>

<nav class="main-nav">
  <ul>
    <li class="active">HOME</li><li>ABOUT</li><li>COURSES</li><li>ONSITE / PRIVATE COURSES</li><li>ONLINE TRAINING</li><li>OUR SERVICES</li><li>STUDENT INFORMATION</li>
  </ul>
</nav>

<section class="hero">
  <div class="hero-photo" role="img" aria-label="Large yellow mining haul truck on a rocky site under a cloudy sky"></div>
  <h1 class="hero-title">Training and experience<br>you can rely on</h1>
  <p class="hero-sub">We use Brontovex and Hiraketo equipment<br>for our training.</p>
  <span class="btn btn-yellow" style="left:144px;top:265px;width:164px;height:39px">Course Calendar</span>
  <span class="btn btn-navy" style="left:313px;top:265px;width:162px;height:39px">Student Handbook</span>
  <div class="hero-dots"><span></span><span class="on"></span><span></span></div>
  <svg class="hero-curve" width="1200" height="496" viewBox="0 0 1200 496">
    <path d="M0 268 C200 480 640 500 1200 268 L1200 280 C660 530 210 530 0 330 Z" fill="var(--navy)"/>
    <path d="M0 330 C210 530 660 530 1200 280 L1200 496 L0 496 Z" fill="#fff"/>
    <path d="M0 296 C205 505 650 515 1200 273" fill="none" stroke="#fff" stroke-width="3"/>
  </svg>
</section>

<h2 class="section-title services-title">Our Services</h2>
<span class="carousel-arrow" style="left:80px"><svg width="14" height="20" viewBox="0 0 14 20"><path d="M11 2 3 10l8 8" fill="none" stroke="#444" stroke-width="2.2"/></svg></span>
<div class="service" style="left:144px"><div class="service-photo" role="img" aria-label="Haul truck on a coal stockpile" style="background:linear-gradient(180deg,#8fb2d2 0%,#c7d3dc 45%,#c9a132 65%,#4c463c 100%)"></div><p class="service-name">Credit Transfers</p></div>
<div class="service" style="left:375px"><div class="service-photo" role="img" aria-label="Gloved hand holding a dust respirator mask" style="background:linear-gradient(135deg,#2f4a6a 0%,#5a6f86 35%,#e8e8e6 60%,#f4f4f2 100%)"></div><p class="service-name">Respirator Fit Testing</p></div>
<div class="service" style="left:605px"><div class="service-photo" role="img" aria-label="Urine sample cup with a test strip" style="background:linear-gradient(135deg,#d8d4cc 0%,#e3c46a 45%,#d9a92e 70%,#c9c4d2 100%)"></div><p class="service-name">Drug and Alcohol<br>Screening Services</p></div>
<div class="service" style="left:835px"><div class="service-photo" role="img" aria-label="Worker in hard hat tying steel reinforcement" style="background:linear-gradient(180deg,#8a9099 0%,#5c5a5a 50%,#7b7570 100%)"></div><p class="service-name">RTO Partnering</p></div>
<span class="carousel-arrow" style="left:1075px"><svg width="14" height="20" viewBox="0 0 14 20"><path d="M3 2l8 8-8 8" fill="none" stroke="#444" stroke-width="2.2"/></svg></span>

<section class="promo">
  <svg class="promo-art" width="1200" height="533" viewBox="0 0 1200 533">
    <defs><linearGradient id="boatGrad" x1="0" y1="0" x2="0" y2="1"><stop offset="0" stop-color="#4f6b4a"/><stop offset=".3" stop-color="#8aa08a"/><stop offset=".55" stop-color="#9fb3b8"/><stop offset="1" stop-color="#2f7b88"/></linearGradient></defs>
    <path d="M778 0 C668 150 668 400 795 533" fill="none" stroke="var(--yellow)" stroke-width="14"/>
    <path d="M800 0 L1200 0 L1200 533 L812 533 C700 400 700 150 800 0 Z" fill="url(#boatGrad)" role="img" aria-label="Man driving a speedboat across a river"/>
  </svg>
  <h2 class="promo-head">Buy now, pay later with Paywise<br><span style="font-weight:700">Buy what you love now. Pay later.</span></h2>
  <p class="promo-text">Choice and flexibility are on your side. Split your purchases into 4 instalments over 6 weeks.</p>
  <h3 class="promo-prize">Give away – Ironhawk Motorcycle<br>or a boat package worth $35,000</h3>
  <p class="promo-small" style="top:307px">All you have to do is click on the button below and complete a Standard 11 refresher to go into the draw.</p>
  <p class="promo-small" style="top:363px">The winner will be announced at the Agrimark Field Day on Saturday the 22nd of June 2024.</p>
  <span class="btn btn-yellow" style="left:144px;top:424px;width:124px;height:38px">Click Here</span>
</section>

<section class="trusted">
  <div class="trusted-photo" role="img" aria-label="Two site workers in hard hats and hi-vis vests checking a clipboard beside a machine"></div>
  <h2 class="section-title trusted-title">Your trusted<br>training partner</h2>
  <p class="trusted-text">We assist our clients in their ongoing quest to achieve zero harm by providing them with the highest calibre of health and safety management advice and personalised training.</p>
</section>

<section class="why">
  <div class="why-photo" role="img" aria-label="Operator in hard hat climbing onto a yellow wheel loader"></div>
  <h2 class="section-title why-title">Why choose us?</h2>
  <p class="why-text">Southern Plantskills Academy consultants have come from the same industries that we consult back to. Our wealth of first hand knowledge and experience enables us to make invaluable contributions to all facets of safety and training in your workplace.</p>
  <div class="why-item" style="top:308px"><span class="why-tick"><svg width="12" height="10" viewBox="0 0 12 10"><path d="M1 5l3.5 3.5L11 1.5" fill="none" stroke="#fff" stroke-width="2"/></svg></span><div><h3>We are passionate</h3><p>We are passionate about Health and Safety.</p></div></div>
  <div class="why-item" style="top:380px"><span class="why-tick"><svg width="12" height="10" viewBox="0 0 12 10"><path d="M1 5l3.5 3.5L11 1.5" fill="none" stroke="#fff" stroke-width="2"/></svg></span><div><h3>We are dependable</h3><p>Let us deliver the right training solution for your business.</p></div></div>
  <div class="why-item" style="top:451px"><span class="why-tick"><svg width="12" height="10" viewBox="0 0 12 10"><path d="M1 5l3.5 3.5L11 1.5" fill="none" stroke="#fff" stroke-width="2"/></svg></span><div><h3>Nationally recognised</h3><p>We are accredited to delivery nationally recognised training.</p></div></div>
</section>

<footer class="site-footer">
  <svg class="footer-curve" width="1200" height="494" viewBox="0 0 1200 494">
    <path d="M0 262 C230 20 700 -20 1200 250 L1200 280 C700 30 230 60 0 300 Z" fill="var(--navy)"/>
    <path d="M0 278 C230 40 700 0 1200 262" fill="none" stroke="#fff" stroke-width="3"/>
    <path d="M0 300 C230 60 700 30 1200 280 L1200 494 L0 494 Z" fill="var(--night)"/>
  </svg>
  <div class="contact" style="left:187px">
    <span class="contact-icon"><svg width="24" height="24" viewBox="0 0 24 24"><path d="M6.6 10.8a15 15 0 0 0 6.6 6.6l2.2-2.2c.3-.3.7-.4 1-.2 1.1.4 2.3.6 3.6.6.6 0 1 .4 1 1V20c0 .6-.4 1-1 1A17 17 0 0 1 3 4c0-.6.4-1 1-1h3.5c.6 0 1 .4 1 1 0 1.3.2 2.5.6 3.6.1.3 0 .7-.2 1z" fill="#fff"/></svg></span>
    <div><h4>Any question at</h4><p>Phone : 1300 555 018</p></div>
  </div>
  <span class="contact-divider" style="left:423px"></span>
  <div class="contact" style="left:462px">
    <span class="contact-icon filled"><svg width="28" height="20" viewBox="0 0 28 20"><rect x="1.5" y="1.5" width="25" height="17" rx="2" fill="none" stroke="var(--navy)" stroke-width="2.5"/><path d="M2 3l12 9 12-9" fill="none" stroke="var(--navy)" stroke-width="2.5"/></svg></span>
    <div><h4>Send your mail at</h4><p>training@plantskills.example</p></div>
  </div>
  <span class="contact-divider" style="left:711px"></span>
  <div class="contact" style="left:751px">
    <span class="contact-icon"><svg width="26" height="22" viewBox="0 0 26 22"><path d="M13 1 1 11h3.5v10h6v-6h5v6h6V11H25z" fill="#fff"/></svg></span>
    <div><p style="margin-top:6px">Address : 24 Ridgeway St, Bowen Vale.<br>Qld 4790.Southern Plantskills Academy<br>Training - RTO number #90217</p></div>
  </div>
  <ul class="footer-nav">
    <li>HOME</li><li>ABOUT</li><li>COURSES</li><li>ONSITE / PRIVATE COURSES</li><li>ONLINE TRAINING</li><li>OUR SERVICES</li><li>STUDENT INFORMATION</li>
  </ul>
  <p class="copyright">© 2024 Southern Plantskills Academy – RTO number #90217.All Rights Reserved &nbsp;|&nbsp; Privacy &nbsp;|&nbsp; Terms of Use</p>
  <div class="socials" role="img" aria-label="Social network links">
    <span style="background:#3b5998"></span><span style="background:#d6246e"></span><span style="background:#0a66c2"></span>
  </div>
</footer>

</body>
</html>
```